Banner Ad Design Project

We need banner ads for a website size:
728 x 90
160 x 90

Look at our website and you can see the color green we use throughout our advertising.

We have copy for 4 ads that should be interchangable

1. EHR me ASAP. Sign up in minutes.
2. Connect. Collaborate. Immediate. Sign up in minutes.
3. No software. No downloads. No charge.
4. EMR + HIE + PMR = FREE

Target Market(s)

Physicians

Industry/Entity Type

Software

```html
<!DOCTYPE html>
<html lang="en">
<head>
<meta charset="utf-8">
<title>Veridon Systems – Skyscraper Banner Set</title>
<link rel="stylesheet" href="https://fonts.googleapis.com/css2?family=Open+Sans:wght@400;600;700&display=swap">
<style>
  :root {
    --stage: #e9e7e3;
    --frame: #e6efdc;
    --panel: #ffffff;
    --brand-green: #7cc243;
    --copy-grey: #5f5f5f;
    --button-top: #8a9a6a;
    --button-bottom: #5d6d44;
    --button-text: #ffffff;
    --team-top: #f3f5fa;
    --team-mid: #b9c3de;
    --team-low: #e6e9f1;
    --lab-top: #f6f6f6;
    --lab-mid: #e4e7ea;
    --lab-low: #f1f2f3;
  }
  * { box-sizing: border-box; margin: 0; padding: 0; }
  html, body { width: 1200px; height: 900px; overflow: hidden; }
  body {
    background: var(--stage);
    font-family: "Open Sans", Arial, sans-serif;
    position: relative;
  }
  .banner-set {
    position: absolute;
    left: 102px;
    top: 40px;
    display: flex;
    gap: 33px;
  }
  .banner {
    position: relative;
    width: 218px;
    height: 820px;
    background: var(--frame);
    padding: 10px;
  }
  .banner__panel {
    position: relative;
    width: 100%;
    height: 100%;
    background: var(--panel);
    border-radius: 14px;
    overflow: hidden;
  }
  .brand {
    position: absolute;
    top: 38px;
    left: 0;
    right: 0;
    display: flex;
    align-items: center;
    justify-content: center;
    gap: 6px;
    white-space: nowrap;
  }
  .brand__dot {
    width: 13px;
    height: 13px;
    border-radius: 50%;
    background: var(--brand-green);
    flex: none;
  }
  .brand__name {
    font-weight: 700;
    font-size: 18px;
    color: var(--brand-green);
    letter-spacing: -0.3px;
  }
  .copy {
    position: absolute;
    left: 0;
    right: 0;
    text-align: center;
    font-weight: 600;
    line-height: 1.15;
  }
  .copy--green { color: var(--brand-green); }
  .copy--grey { color: var(--copy-grey); }
  .headline { top: 176px; font-size: 31px; }
  .subline { top: 250px; font-size: 33px; }
  .headline--stack { top: 143px; font-size: 24px; line-height: 1.2; }
  .subline--low { top: 248px; }
  .list { top: 167px; font-size: 24px; line-height: 1.9; }
  .equation { top: 176px; font-size: 18px; }
  .free { top: 236px; font-size: 58px; font-weight: 700; }
  .visual {
    position: absolute;
    left: 0;
    right: 0;
  }
  .visual--team {
    top: 438px;
    height: 200px;
    background: linear-gradient(180deg, var(--team-top) 0%, var(--team-mid) 45%, var(--team-low) 85%, var(--panel) 100%);
  }
  .visual--lab {
    top: 408px;
    height: 232px;
    background: linear-gradient(180deg, var(--lab-top) 0%, var(--lab-mid) 60%, var(--lab-low) 100%);
  }
  .cta {
    position: absolute;
    left: 12px;
    right: 12px;
    top: 687px;
    height: 45px;
    border-radius: 5px;
    background: linear-gradient(180deg, var(--button-top), var(--button-bottom));
    color: var(--button-text);
    font-size: 16px;
    font-weight: 400;
    display: flex;
    align-items: center;
    justify-content: center;
  }
</style>
</head>
<body>
  <main class="banner-set">
    <section class="banner">
      <div class="banner__panel">
        <div class="brand"><span class="brand__dot"></span><span class="brand__name">Veridon Systems</span></div>
        <p class="copy copy--green headline">EHR me<br>ASAP</p>
        <p class="copy copy--grey subline">Sign up in<br>minutes</p>
        <div class="visual visual--team" role="img" aria-label="Photo of a group of smiling doctors and nurses looking up"></div>
        <div class="cta">Sign Up For Free</div>
      </div>
    </section>

    <section class="banner">
      <div class="banner__panel">
        <div class="brand"><span class="brand__dot"></span><span class="brand__name">Veridon Systems</span></div>
        <p class="copy copy--green headline--stack">Connect<br>Collaborate<br>Immediately</p>
        <p class="copy copy--grey subline subline--low">Sign up in<br>minutes</p>
        <div class="visual visual--team" role="img" aria-label="Photo of a group of smiling doctors and nurses looking up"></div>
        <div class="cta">Sign Up For Free</div>
      </div>
    </section>

    <section class="banner">
      <div class="banner__panel">
        <div class="brand"><span class="brand__dot"></span><span class="brand__name">Veridon Systems</span></div>
        <p class="copy list">
          <span class="copy--green">No software</span><br>
          <span class="copy--grey">No downloads</span><br>
          <span class="copy--green">No charge</span>
        </p>
        <div class="visual visual--lab" role="img" aria-label="Photo of colourful test tubes in a rack beside a laboratory flask"></div>
        <div class="cta">Sign Up For Free</div>
      </div>
    </section>

    <section class="banner">
      <div class="banner__panel">
        <div class="brand"><span class="brand__dot"></span><span class="brand__name">Veridon Systems</span></div>
        <p class="copy copy--green equation">EMR + HIE + PHR =</p>
        <p class="copy copy--grey free">FREE</p>
        <div class="visual visual--lab" role="img" aria-label="Photo of colourful test tubes in a rack beside a laboratory flask"></div>
        <div class="cta">Sign Up For Free</div>
      </div>
    </section>
  </main>
</body>
</html>
```